Harcourt Power Gym Chronic Pain Flyer

Double sided DL flyer required to promote a strength training studio to sufferers of chronic pain. Flyer will be displayed in osteopathy, chiropractic and massage clinics. Flyer should be clean, professional and appeal to an older (40+) demographic.

Target Market(s)

Chronic pain sufferers. Age 40+

Industry/Entity Type

Health And Wellness

Colors

Designer to choose colors to be used in the design.

Requirements
Must have
• See attached files for text copy and logo. Image(s) of people strength training with a coach or personal trainer, as well as images depicting pain in common parts of the body (such as those pictured in the supplied mock up)
• website address: harcourtpowergym.com.au
• phone number : 0458 214 963
• Street address: 3/14 Birchwood Rd, Harcourt
Nice to have
• Images such as in the attached files.

```html
<!DOCTYPE html>
<html lang="en">
<head>
<meta charset="utf-8">
<title>Harcourt Power Gym – DL Flyer</title>
<link href="https://fonts.googleapis.com/css2?family=Montserrat:wght@400;500;700;800;900&family=Raleway:wght@400&display=swap" rel="stylesheet">
<style>
  :root{
    --page:#f2f2f2;
    --ink:#1f1f20;
    --panel-dark:#222223;
    --red:#d8262b;
    --red-band:#c4302b;
    --silver:#d6d6d6;
    --white:#ffffff;
  }
  html,body{margin:0;padding:0;overflow:hidden;}
  body{width:1200px;height:1200px;background:var(--page);position:relative;font-family:'Montserrat',sans-serif;}
  .flyer{position:absolute;top:239px;width:350px;height:740px;overflow:hidden;background:var(--panel-dark);}
  .flyer--front{left:232px;}
  .flyer--back{left:636px;}

  .photo{position:absolute;left:0;top:0;width:350px;height:360px;}
  .photo--back-pain{background:radial-gradient(ellipse 60px 90px at 155px 260px,rgba(220,40,40,.8),rgba(220,40,40,0) 100%),linear-gradient(135deg,#6a6a6a 0%,#a9a9a9 45%,#e4e4e4 100%);}
  .photo--knee-pain{background:radial-gradient(ellipse 80px 130px at 300px 240px,rgba(225,50,50,.85),rgba(225,50,50,0) 100%),linear-gradient(90deg,#f4f4f4 0%,#e6e6e6 55%,#9a9a9a 100%);}

  .dark-shape{position:absolute;left:0;width:350px;}
  .flyer--front .dark-shape{top:310px;height:430px;}
  .flyer--back .dark-shape{top:316px;height:424px;}

  .centered{position:absolute;left:0;width:350px;text-align:center;}

  .brand-name{font-family:'Montserrat',sans-serif;font-weight:800;text-transform:uppercase;letter-spacing:1px;display:flex;align-items:center;gap:8px;}
  .brand-name .dot{width:10px;height:10px;border-radius:50%;background:currentColor;display:inline-block;}
  .flyer--front .brand-name{position:absolute;top:392px;left:0;width:350px;justify-content:center;color:var(--silver);font-size:21px;}
  .flyer--back .brand-name{position:absolute;top:72px;left:16px;color:#555556;font-size:17px;}

  .headline--light{top:488px;font-family:'Raleway',sans-serif;font-weight:400;color:#e9e9e9;font-size:46px;line-height:40px;margin:0;text-transform:uppercase;}
  .divider{position:absolute;top:617px;left:45px;width:260px;height:1px;background:linear-gradient(90deg,rgba(255,255,255,0),rgba(255,255,255,.35),rgba(255,255,255,0));}

  .contact{color:var(--white);}
  .contact .phone{display:flex;justify-content:center;align-items:center;gap:6px;margin:0;}
  .contact .address{display:flex;justify-content:center;align-items:flex-start;gap:6px;margin:4px 0 0;line-height:20px;}
  .contact svg{flex:none;}
  .flyer--front .contact{top:626px;}
  .flyer--front .phone{font-size:27px;font-weight:500;}
  .flyer--front .address{font-size:16px;font-weight:500;}
  .flyer--back .contact{top:602px;}
  .flyer--back .phone{font-size:26px;font-weight:700;}
  .flyer--back .address{font-size:17px;font-weight:400;}

  .web-band{position:absolute;left:0;bottom:0;width:350px;height:30px;background:var(--red-band);color:var(--white);display:flex;justify-content:center;align-items:center;font-size:16px;}
  .web-band strong{font-weight:700;}
  .web-band span{font-weight:400;}

  .headline--heavy{position:absolute;left:20px;top:184px;margin:0;font-weight:900;color:var(--ink);font-size:33px;line-height:31px;letter-spacing:-.5px;text-transform:uppercase;}
  .subline{position:absolute;left:22px;top:278px;margin:0;color:var(--red);font-weight:700;font-size:16px;line-height:17px;text-transform:uppercase;}

  .body-copy{top:357px;color:#e6e6e6;font-size:12.3px;line-height:15px;font-weight:500;}
  .body-copy p{margin:0 0 14px;padding:0 24px;}
  .cta{top:526px;margin:0;color:var(--red);font-weight:900;font-size:16px;line-height:15px;text-transform:uppercase;}
</style>
</head>
<body>

<section class="flyer flyer--front" aria-label="Flyer front">
  <div class="photo photo--back-pain" role="img" aria-label="Black and white photo of a man holding his lower back, spine highlighted in red"></div>
  <svg class="dark-shape" viewBox="0 0 350 430" preserveAspectRatio="none"><path d="M0 38 Q175 -18 350 38 V430 H0 Z" fill="#222223"/></svg>
  <div class="brand-name"><span class="dot"></span>Harcourt Power Gym</div>
  <h1 class="centered headline--light">Health<br>Through<br>Strength</h1>
  <div class="divider"></div>
  <div class="centered contact">
    <p class="phone"><svg width="18" height="18" viewBox="0 0 24 24"><path d="M6.6 10.8a15 15 0 0 0 6.6 6.6l2.2-2.2a1 1 0 0 1 1-.25 11 11 0 0 0 3.6.6 1 1 0 0 1 1 1V20a1 1 0 0 1-1 1A17 17 0 0 1 3 4a1 1 0 0 1 1-1h3.5a1 1 0 0 1 1 1 11 11 0 0 0 .6 3.6 1 1 0 0 1-.25 1z" fill="#d8262b"/></svg>0458 214 963</p>
    <p class="address"><svg width="14" height="18" viewBox="0 0 14 18"><path d="M7 1a6 6 0 0 0-6 6c0 4.5 6 10 6 10s6-5.5 6-10a6 6 0 0 0-6-6z" fill="none" stroke="#d8262b" stroke-width="2"/><circle cx="7" cy="7" r="2" fill="#d8262b"/></svg><span>3/14 Birchwood Rd,<br>Harcourt, VIC, 3099</span></p>
  </div>
  <div class="web-band"><strong>harcourtpowergym</strong><span>.com.au</span></div>
</section>

<section class="flyer flyer--back" aria-label="Flyer back">
  <div class="photo photo--knee-pain" role="img" aria-label="Black and white photo of hands holding a knee, the joint glowing red"></div>
  <svg class="dark-shape" viewBox="0 0 350 424" preserveAspectRatio="none"><path d="M0 34 Q175 -16 350 34 V424 H0 Z" fill="#222223"/></svg>
  <div class="brand-name"><span class="dot"></span>Harcourt Power Gym</div>
  <h2 class="headline--heavy">Health<br>Through<br>Strength</h2>
  <p class="subline">You don’t have to<br>live in pain</p>
  <div class="centered body-copy">
    <p>strength training has been shown to improve many chronic pain conditions and is now being routinely recommended by medical and health professionals.</p>
    <p>Our private studio provides high quality strength training by expert strength coaches.</p>
    <p>We’ve helped countless people improve or eliminate chronic pain.</p>
  </div>
  <p class="centered cta">Contact us today and<br>find out how<br>we can help you.</p>
  <div class="centered contact">
    <p class="phone"><svg width="20" height="20" viewBox="0 0 24 24"><path d="M6.6 10.8a15 15 0 0 0 6.6 6.6l2.2-2.2a1 1 0 0 1 1-.25 11 11 0 0 0 3.6.6 1 1 0 0 1 1 1V20a1 1 0 0 1-1 1A17 17 0 0 1 3 4a1 1 0 0 1 1-1h3.5a1 1 0 0 1 1 1 11 11 0 0 0 .6 3.6 1 1 0 0 1-.25 1z" fill="#d8262b"/></svg>0458 214 963</p>
    <p class="address"><svg width="14" height="18" viewBox="0 0 14 18"><path d="M7 1a6 6 0 0 0-6 6c0 4.5 6 10 6 10s6-5.5 6-10a6 6 0 0 0-6-6z" fill="none" stroke="#d8262b" stroke-width="2"/><circle cx="7" cy="7" r="2" fill="#d8262b"/></svg><span>3/14 Birchwood Rd,<br>Harcourt, VIC, 3099</span></p>
  </div>
  <div class="web-band"><strong>harcourtpowergym</strong><span>.com.au</span></div>
</section>

</body>
</html>
```